Business Card Design for Occupational Medicine Start Up Company

We need to design a professional business card. We are a healthcare company providing occupational medicine services to blue collar industries. We are professional, efficient and high quality service providers.

Target Market(s)

Blue Collar Industry: Shipbuilding, Ports, Trucking Companies; The Executives and Safety Officers for these companies

Industry/Entity Type

Healthcare

Contact Information for Business Card

Logo, Name, Title, Email, Phone

Other font styles liked:
• Please match our Brand Guide

Requirements
Must have
• Our Company Colors and Logo

```html
<!DOCTYPE html>
<html lang="en">
<head>
<meta charset="utf-8">
<title>ShiftWell Clinics – Business Card</title>
<link href="https://fonts.googleapis.com/css2?family=Montserrat:wght@700&family=Open+Sans:wght@400&display=swap" rel="stylesheet">
<style>
  :root {
    --stage: #2c2c2c;
    --card: #e8e9eb;
    --navy: #2b3a8c;
    --sky: #29a9e0;
    --amber: #f6ae3f;
    --ink: #4a4f5c;
    --rule: #5a6080;
  }
  * { margin: 0; padding: 0; box-sizing: border-box; }
  html, body { width: 1200px; height: 1107px; overflow: hidden; }
  body {
    background: var(--stage);
    position: relative;
    font-family: "Open Sans", sans-serif;
  }
  .card {
    position: absolute;
    left: 236px;
    width: 803px;
    height: 461px;
    background: var(--card);
    overflow: hidden;
  }
  .card--front { top: 69px; }
  .card--back { top: 579px; }

  .stripes { position: absolute; left: 0; width: 100%; }
  .stripes span { display: block; width: 100%; }
  .stripes .navy { height: 4px; background: var(--navy); }
  .stripes .amber { height: 3px; background: var(--amber); }
  .stripes .sky { height: 4px; background: var(--sky); }
  .stripes .gap { height: 2px; background: var(--card); }
  .card--front .stripes { top: 445px; }
  .card--back .stripes { top: 338px; }

  .mark {
    position: absolute;
    left: 150px; top: 220px;
    display: flex; align-items: center; gap: 12px;
    font-family: "Montserrat", sans-serif;
    font-weight: 700;
    font-size: 30px;
    letter-spacing: 1px;
    color: var(--navy);
  }
  .mark .dot {
    width: 22px; height: 22px; border-radius: 50%;
    background: var(--sky);
  }
  .divider {
    position: absolute;
    left: 426px; top: 147px;
    width: 2px; height: 188px;
    background: var(--rule);
  }
  .contact {
    position: absolute;
    left: 484px; top: 140px;
    color: var(--ink);
  }
  .contact .name {
    font-size: 24px; color: var(--navy); line-height: 1.3;
  }
  .contact .name .last { color: var(--amber); }
  .contact .title { font-size: 16px; margin-bottom: 12px; }
  .contact .line {
    display: flex; align-items: center; gap: 10px;
    font-size: 17px; line-height: 27px;
  }
  .contact .line svg { width: 13px; height: 13px; fill: var(--navy); flex: none; }
  .contact .line .accent { color: var(--amber); }
  .contact .address { margin-top: 10px; font-size: 17px; line-height: 27px; }

  .back-brand {
    position: absolute;
    left: 0; right: 0; top: 150px;
    text-align: center;
    font-family: "Montserrat", sans-serif;
    font-weight: 700;
    color: var(--navy);
  }
  .back-brand .dot {
    width: 44px; height: 44px; border-radius: 50%;
    background: var(--sky);
    margin: 0 auto 18px;
  }
  .back-brand .name { font-size: 40px; letter-spacing: 1px; line-height: 1; }
  .back-brand .sub { font-size: 40px; letter-spacing: 1px; line-height: 1; }
  .back-brand .sub small { display: block; font-size: 19px; letter-spacing: 5px; margin-top: 6px; }
</style>
</head>
<body>
  <section class="card card--front">
    <div class="mark"><span class="dot"></span>SHIFTWELL</div>
    <div class="divider"></div>
    <div class="contact">
      <p class="name">Sela <span class="last">Marin</span></p>
      <p class="title">Directeur</p>
      <p class="line">
        <svg viewBox="0 0 16 16" aria-hidden="true"><path d="M3.5 1l2.5 3-1.5 2c1 2 3 4 5 5l2-1.5 3 2.5-1.5 2.5C7 15 1 9 1 2.5z"/></svg>
        +0212 0555 204 118
      </p>
      <p class="line">
        <svg viewBox="0 0 16 16" aria-hidden="true"><path d="M1 3h14v10H1z M1 3l7 6 7-6" /></svg>
        s.marin@shiftwell.ma
      </p>
      <p class="line">
        <svg viewBox="0 0 16 16" aria-hidden="true"><circle cx="8" cy="8" r="7"/></svg>
        <span>www.<span class="accent">shiftwell</span>.ma</span>
      </p>
      <p class="address">PO BOX 51870 Westmere<br>Calder, AB T4K-3R</p>
    </div>
    <div class="stripes"><span class="navy"></span><span class="gap"></span><span class="amber"></span><span class="gap"></span><span class="sky"></span></div>
  </section>

  <section class="card card--back">
    <div class="back-brand">
      <div class="dot"></div>
      <p class="name">SHIFTWELL</p>
      <p class="sub"><small>CLINICS</small></p>
    </div>
    <div class="stripes"><span class="navy"></span><span class="gap"></span><span class="amber"></span><span class="gap"></span><span class="sky"></span></div>
  </section>
</body>
</html>
```